RESIDENTIAL CONSTRUCTION

We are a company that specializes in building custom residential homes, the design should also emphasize that quality and service is our priority.

Industry/Entity Type

Construction Company

Contact Information for Business Card

Contact Person: Marcus Lindqvist
Company Address: 273 West Alder Ave San Jose , Ca 95380
Phone Number : 408-731-2946
Email Address: Stoneridgehomes517@mailvista.net

Font styles to use
Sans Serif

Colors
ec1f27

Requirements
Must have
• CSLB # 7362015
Nice to have
• needs to have same color as logo i uploaded, we will be printing these on a clear plastic card.

```html
<!DOCTYPE html>
<html lang="en">
<head>
<meta charset="utf-8">
<title>Stoneridge Homes — Business Card</title>
<link href="https://fonts.googleapis.com/css2?family=Roboto:wght@400;700;900&display=swap" rel="stylesheet">
<style>
  :root {
    --brand-red: #ec1f27;
    --ink: #3a3a3a;
    --ink-soft: #5a5a5a;
    --card: #ffffff;
  }
  * { margin: 0; padding: 0; box-sizing: border-box; }
  html, body {
    width: 1200px;
    height: 758px;
    overflow: hidden;
    background: var(--card);
  }
  .business-card {
    position: relative;
    width: 1200px;
    height: 758px;
    background: var(--card);
    font-family: "Roboto", Arial, sans-serif;
    color: var(--ink);
  }
  .brand {
    position: absolute;
    top: 110px;
    right: 150px;
    display: flex;
    align-items: center;
    gap: 18px;
  }
  .brand-square {
    width: 64px;
    height: 64px;
    background: var(--brand-red);
  }
  .brand-name {
    font-weight: 900;
    font-size: 58px;
    letter-spacing: 1px;
    color: var(--brand-red);
    text-transform: uppercase;
    line-height: 1;
  }
  .contact-person {
    position: absolute;
    left: 150px;
    top: 470px;
  }
  .person-name {
    font-weight: 700;
    font-size: 34px;
    color: var(--brand-red);
    text-transform: uppercase;
    letter-spacing: 0.5px;
    margin-bottom: 36px;
  }
  .contact-list { list-style: none; }
  .contact-item {
    display: flex;
    align-items: center;
    gap: 20px;
    font-size: 25px;
    color: var(--ink-soft);
    line-height: 38px;
  }
  .contact-icon { width: 22px; height: 22px; flex: none; }
  .office-details {
    position: absolute;
    right: 110px;
    top: 490px;
    text-align: right;
    font-size: 24px;
    line-height: 32px;
    color: var(--ink);
  }
  .license { margin-top: 12px; }
</style>
</head>
<body>
<main class="business-card">
  <header class="brand">
    <div class="brand-square"></div>
    <span class="brand-name">Stoneridge Homes</span>
  </header>

  <section class="contact-person">
    <h1 class="person-name">Marcus Lindqvist</h1>
    <ul class="contact-list">
      <li class="contact-item">
        <svg class="contact-icon" viewBox="0 0 24 24" aria-hidden="true"><path fill="var(--brand-red)" d="M6.6 10.8a15.1 15.1 0 0 0 6.6 6.6l2.2-2.2a1 1 0 0 1 1-.25 11.4 11.4 0 0 0 3.6.57 1 1 0 0 1 1 1V20a1 1 0 0 1-1 1A17 17 0 0 1 3 4a1 1 0 0 1 1-1h3.5a1 1 0 0 1 1 1c0 1.25.2 2.45.57 3.57a1 1 0 0 1-.25 1z"/></svg>
        <span>408-731-2946</span>
      </li>
      <li class="contact-item">
        <svg class="contact-icon" viewBox="0 0 24 24" aria-hidden="true"><rect x="2" y="5" width="20" height="14" fill="var(--brand-red)"/><path d="M2 5l10 8 10-8" fill="none" stroke="#fff" stroke-width="1.8"/></svg>
        <span>Stoneridgehomes517@mailvista.net<br>Stoneridgehomes.com</span>
      </li>
      <li class="contact-item">
        <svg class="contact-icon" viewBox="0 0 24 24" aria-hidden="true"><circle cx="12" cy="12" r="10" fill="var(--brand-red)"/><path d="M2 12h20M12 2c3 3 3 17 0 20M12 2c-3 3-3 17 0 20" fill="none" stroke="#fff" stroke-width="1.4"/></svg>
        <span>www.stoneridgehomes.com</span>
      </li>
    </ul>
  </section>

  <address class="office-details" style="font-style: normal;">
    <div>273 West Alder Ave San</div>
    <div>Jose, Ca 95380</div>
    <div class="license">CSLB # 7362015</div>
  </address>
</main>
</body>
</html>
```